Theater Ad

A graphic for advertising in an indoor theater.
Target Market(s)
Parents of infants, toddlers, tweens and teens.
Industry/Entity Type
Pediatric Ophthalmology
Font styles to use
Sans Serif
Colors
EB3D1F
EC4F4E
F09395
F8D3D4
FCEDEE
Requirements
Must have
- Use the copy, color scheme, and photos shown in the attached older billboard advertisement, but in a new design for the theater.

Nice to have
- New design with both logos included

Should not have
- Just a single logo - must include both logos

```html
<!DOCTYPE html>
<html lang="en">
<head>
<meta charset="utf-8">
<title>Theater Ad – Pediatric Ophthalmology</title>
<link rel="stylesheet" href="https://fonts.googleapis.com/css2?family=Bebas+Neue&family=Oswald:wght@300&family=Poppins:wght@300;400;600;700&display=swap">
<style>
  :root {
    --brand-blue: #1a72b8;
    --brand-red: #e31e25;
    --brand-red-deep: #c00d14;
    --ink: #1c1c1c;
    --paper: #ffffff;
    --backdrop: #e4e4e4;
    --photo-light: #d9d6cf;
    --photo-dark: #4d5a4a;
  }
  * { margin: 0; padding: 0; box-sizing: border-box; }
  html, body { width: 900px; height: 1200px; overflow: hidden; }
  body {
    background: radial-gradient(ellipse at center, #f2f2f2 0%, var(--backdrop) 70%);
    font-family: "Poppins", sans-serif;
  }
  .ad {
    position: absolute;
    left: 20px; top: 358px;
    width: 860px; height: 484px;
    background: var(--paper);
    box-shadow: 0 18px 40px rgba(0,0,0,0.28);
    overflow: hidden;
  }
  .ad-shapes { position: absolute; inset: 0; }
  .portrait-frame {
    position: absolute;
    left: 21px; top: 18px;
    width: 296px; height: 296px;
    border-radius: 50%;
    background: var(--paper);
  }
  .portrait-ring {
    position: absolute;
    left: 29px; top: 26px;
    width: 280px; height: 280px;
    border-radius: 50%;
    border: 18px solid var(--brand-red);
    background: var(--paper);
  }
  .portrait-photo {
    position: absolute;
    left: 51px; top: 48px;
    width: 236px; height: 236px;
    border-radius: 50%;
    background: radial-gradient(circle at 55% 40%, var(--photo-light) 0%, #a9a39a 45%, var(--photo-dark) 100%);
  }
  .text { position: absolute; white-space: nowrap; line-height: 1; }
  .doctor-name {
    left: 326px; top: 59px;
    color: var(--paper);
    font-weight: 700; font-size: 40px; line-height: 42px;
    letter-spacing: 0.5px;
  }
  .doctor-degrees {
    left: 326px; top: 146px;
    color: var(--paper); font-weight: 400; font-size: 23px;
  }
  .divider {
    position: absolute; left: 621px; top: 64px;
    width: 2px; height: 114px; background: var(--paper);
  }
  .specialty {
    left: 644px; color: var(--paper);
    font-weight: 600; font-size: 17px; line-height: 21px;
  }
  .specialty-en { top: 62px; }
  .specialty-es { top: 126px; }
  .credential { top: 214px; color: var(--paper); }
  .credential-label { display: block; font-weight: 400; font-size: 17px; }
  .credential-value { display: block; font-weight: 700; font-size: 34px; margin-top: 4px; }
  .credential-residency { left: 326px; }
  .credential-fellowship { left: 486px; }
  .credential-board { left: 646px; }
  .language {
    left: 71px; top: 318px;
    color: var(--ink); font-weight: 700; font-size: 22px; line-height: 26px;
  }
  .clinic-name {
    display: flex; align-items: center; gap: 7px;
    color: var(--brand-blue); font-weight: 700; font-size: 17px; line-height: 20px;
  }
  .clinic-name::before {
    content: ""; flex: none;
    width: 14px; height: 14px; border-radius: 50%;
    background: var(--brand-blue);
  }
  .clinic-optical { left: 218px; top: 330px; }
  .clinic-eyecare { left: 403px; top: 330px; }
  .tagline-strong {
    left: 609px; top: 318px;
    color: var(--brand-red); font-weight: 700; font-size: 27px;
  }
  .tagline-light {
    left: 609px; top: 350px;
    color: var(--ink); font-family: "Oswald", sans-serif; font-weight: 300; font-size: 29px;
    letter-spacing: 0.5px;
  }
  .call {
    left: 50px; top: 414px;
    font-family: "Bebas Neue", sans-serif; font-size: 36px;
    color: var(--paper);
  }
  .call-label { color: var(--brand-red); }
  .web {
    left: 428px; top: 408px;
    font-family: "Bebas Neue", sans-serif; font-size: 38px; letter-spacing: 1.4px;
    color: var(--ink);
  }
  .web-domain { color: var(--brand-blue); }
</style>
</head>
<body>
  <main class="ad">
    <svg class="ad-shapes" width="860" height="484" viewBox="0 0 860 484" aria-hidden="true">
      <path class="name-band" d="M230 36 H811 Q825 36 825 50 V189 H230 Z" fill="var(--brand-blue)"/>
      <path class="credential-band" d="M230 189 H825 V281 Q825 295 811 295 H230 Z" fill="var(--brand-red)"/>
      <rect class="credential-band-accent" x="474" y="189" width="160" height="106" fill="var(--brand-red-deep)"/>
      <path class="contact-band" d="M0 400 H366 Q392 400 402 424 L429 484 H0 Z" fill="var(--brand-blue)"/>
    </svg>

    <div class="portrait-frame"></div>
    <div class="portrait-ring"></div>
    <div class="portrait-photo" role="img" aria-label="Portrait photo of the doctor seated at a desk, wearing glasses and a polka-dot jacket"></div>

    <h1 class="text doctor-name">MARINA<br>KOSTELIC</h1>
    <p class="text doctor-degrees">M.D, M.P.H.</p>
    <span class="divider"></span>
    <p class="text specialty specialty-en">Pediatric<br>Opthalmologist</p>
    <p class="text specialty specialty-es">Oftalmologia<br>Pediatrica</p>

    <p class="text credential credential-residency"><span class="credential-label">U.S. Residency</span><span class="credential-value">Trained</span></p>
    <p class="text credential credential-fellowship"><span class="credential-label">U.S. Fellowship</span><span class="credential-value">Trained</span></p>
    <p class="text credential credential-board"><span class="credential-label">American Board</span><span class="credential-value">Certified</span></p>

    <p class="text language">Se Habla<br>Español</p>
    <p class="text clinic-name clinic-optical">Little Lens<br>Optical</p>
    <p class="text clinic-name clinic-eyecare">Bright Sight<br>Eye Care</p>

    <p class="text tagline-strong">WE HELP KIDS</p>
    <p class="text tagline-light">SEE BETTER!</p>

    <p class="text call"><span class="call-label">CALL US NOW:</span> (555) 014-2273</p>
    <p class="text web">WWW.<span class="web-domain">KIDSVISIONCLINIC</span>.COM</p>
  </main>
</body>
</html>
```